Wordpress Design Project (Dunmore)

We need a wordpress design for an established auction and real estate company based in Virginia. The winning design will incorporate the colors of logo (red and black) creatively with an accent color in a very professional and clean layout.

Industry/Entity Type

Real Estate

Requirements
Must have
• We will require winning designer to provide a layered PSD (Adobe photoshop) concept file, along with any non-standard font files used.

Horizontal Navigation menu with these links:
Home - Upcoming Auctions - Past Auctions - For Sale- Consignments - About Us - Highlights - Contact Us

A slideshow element on the home page using the placeholder image provided.

Sidebar widgets to be included are: Email sign-up form - Featured Auctions - Featured Assets for Sale (see attached for visual of these widgets)

attached logos in footer with company contact info

```html
<!DOCTYPE html>
<html lang="en">
<head>
<meta charset="utf-8">
<title>Dunmore Enterprises</title>
<link href="https://fonts.googleapis.com/css2?family=Open+Sans:wght@400;600;700&display=swap" rel="stylesheet">
<style>
:root{
  --red:#e9291d;
  --dark:#2b2b2b;
  --ink:#333;
  --muted:#666;
  --panel:#f0f0f0;
  --white:#fff;
}
*{margin:0;padding:0;box-sizing:border-box}
html,body{width:781px;height:1200px;overflow:hidden;background:var(--white);font-family:"Open Sans",Arial,sans-serif;color:var(--ink)}
.page{position:relative;width:781px;height:1200px}
.abs{position:absolute}
.social{top:13px;left:588px;display:flex;gap:6px}
.social span{width:22px;height:22px;border-radius:50%;display:block}
.brand{top:46px;left:87px;display:flex;align-items:center;gap:8px}
.brand-mark{width:26px;height:26px;background:var(--red)}
.brand-name{font-size:19px;font-weight:600;color:var(--dark)}
.search{top:64px;left:534px;width:162px;height:20px;border:1px solid #cfcfcf;border-radius:3px;background:linear-gradient(#f4f4f4,#e6e6e6);font-size:5px;color:#aaa;padding:5px 7px}
.search svg{position:absolute;right:6px;top:4px}
.nav{top:98px;left:0;width:781px;height:36px;background:var(--red);display:flex;justify-content:center;align-items:center;font-size:8px;color:var(--white)}
.nav span.sep{margin:0 14px}
.hero{top:134px;left:0;width:781px;height:309px;background:linear-gradient(180deg,#8fb2da 0%,#c9c1a8 45%,#8a9a5a 72%,#4e7a2a 100%)}
.hero-title{top:178px;left:174px;color:var(--white);font-size:20px;line-height:1}
.hero-sub{top:205px;left:177px;color:var(--white);font-size:12px}
.hero-frame{top:194px;left:394px;width:302px;height:193px;background:var(--white);padding:6px}
.hero-frame div{width:100%;height:100%;background:linear-gradient(180deg,#b9d7ef 0%,#dce9f2 45%,#8fa7bd 55%,#7fa0b8 70%,#5e8a3c 85%,#3f6d24 100%)}
.dots{top:412px;left:360px;display:flex;gap:4px}
.dots span{width:12px;height:12px;border-radius:50%;background:#222;border:1px solid #111}
.dots span.on{background:#8b1a12}
.panel{top:443px;left:78px;width:624px;height:697px;background:var(--panel)}
h2{font-weight:400;color:var(--red);font-size:14.5px}
.lorem{font-size:6.4px;line-height:11.7px;color:#555;text-align:justify}
.welcome-img{top:503px;left:92px;width:193px;height:124px;background:var(--white);border:1px solid #ddd;padding:6px}
.welcome-img div{width:100%;height:100%;background:radial-gradient(circle at 50% 45%,#c9a97b,#efe6d4 70%,#fff)}
.side{top:473px;left:554px;width:142px;height:259px;background:var(--dark);color:var(--white);text-align:center}
.side-head{background:var(--red);height:28px;font-size:10px;font-weight:600;line-height:28px}
.side-session{font-size:7.2px;text-align:left;padding:10px 14px 0;line-height:12px}
.side-img{margin:8px auto 0;width:114px;height:72px;background:linear-gradient(160deg,#5a7ea6,#c8ccd2 50%,#4b4b4b)}
.side-btn{margin:4px auto 0;width:92px;height:22px;background:var(--red);font-size:7.5px;font-weight:600;line-height:22px}
.side-label{color:var(--red);font-size:7.5px;font-weight:600;margin-top:8px}
.side-text{font-size:6.4px;line-height:11.5px}
.card{width:143px}
.card-img{height:78px}
.card-title{color:var(--red);font-size:10px;font-weight:600;line-height:14px;margin-top:18px;height:36px}
.card-date{font-size:7.6px;color:#222;margin-top:2px}
.card .lorem{margin-top:9px;line-height:11.7px}
.partners{top:1038px;left:78px;width:624px;text-align:center}
.rule{top:1056px;left:78px;width:624px;height:1px;background:#ddd}
.badges{top:1063px;left:110px;width:580px;display:flex;justify-content:space-between;align-items:center}
.badge{background:#3a3a3a}
.footer{top:1140px;left:0;width:781px;height:60px;background:var(--red);color:var(--white);text-align:center;font-size:6.5px}
.footer-nav{padding-top:20px;display:flex;justify-content:center}
.footer-nav span.sep{margin:0 12px}
.footer-copy{margin-top:13px}
</style>
</head>
<body>
<div class="page">
  <div class="abs social" aria-label="Social links">
    <span style="background:#e62117"></span><span style="background:#1da1e2"></span><span style="background:#1d77b5"></span><span style="background:#3b5998"></span>
  </div>
  <div class="abs brand"><span class="brand-mark"></span><span class="brand-name">Dunmore Enterprises</span></div>
  <div class="abs search">Search
    <svg width="12" height="12" viewBox="0 0 12 12"><circle cx="5" cy="5" r="3.5" fill="none" stroke="#777" stroke-width="1.4"/><line x1="7.5" y1="7.5" x2="11" y2="11" stroke="#777" stroke-width="1.6"/></svg>
  </div>

  <nav class="abs nav">
    <span>Home</span><span class="sep">|</span><span>Upcoming Auctions</span><span class="sep">|</span><span>Past Auctions</span><span class="sep">|</span><span>For Sale</span><span class="sep">|</span><span>Consignments</span><span class="sep">|</span><span>About Us</span><span class="sep">|</span><span>Highlights</span><span class="sep">|</span><span>Contact Us</span>
  </nav>

  <div class="abs hero" role="img" aria-label="Large colonial house with white columns among palm trees and a green lawn"></div>
  <div class="abs hero-title">We are an established</div>
  <div class="abs hero-sub">auction and real estate company</div>
  <div class="abs hero-frame"><div role="img" aria-label="Lake view with a wooden pier and tall grass"></div></div>
  <div class="abs dots"><span></span><span class="on"></span><span class="on"></span><span class="on"></span></div>

  <div class="abs panel"></div>
  <h2 class="abs" style="top:470px;left:87px">Welcome to Dunmore Enterprises</h2>
  <div class="abs" style="top:496px;left:87px;width:453px;height:1px;background:#ddd"></div>
  <div class="abs welcome-img"><div role="img" aria-label="Miniature house with an auction gavel on banknotes"></div></div>
  <p class="abs lorem" style="top:505px;left:294px;width:246px">Lorem ipsum dolor sit amet, consectetur adipisicing elit, sed do eiusmod tempor incididunt ut labore et dolore magna aliqua. Ut enim ad minim veniam, quis nostrud exercitation ullamco laboris nisi ut aliquip ex ea commodo consequat. Duis aute irure dolor in reprehenderit in voluptate velit esse cillum dolore eu fugiat nulla pariatur. Excepteur sint occaecat cupidatat non proident, sunt in culpa qui officia deserunt mollit anim id est laborum.Lorem ipsum dolor sit amet, consectetur adipisicing elit, sed do eiusmod tempor incididunt ut labore et dolore magna aliqua. Ut enim ad minim veniam, quis nostrud exercitation ullamco laboris nisi ut aliquip ex ea commodo consequat.</p>
  <p class="abs lorem" style="top:641px;left:85px;width:455px">Lorem ipsum dolor sit amet, consectetur adipisicing elit, sed do eiusmod tempor incididunt ut labore et dolore magna aliqua. Ut enim ad minim veniam, quis nostrud exercitation ullamco laboris nisi ut aliquip ex ea commodo consequat. Duis aute irure dolor in reprehenderit in voluptate velit esse cillum dolore eu fugiat nulla pariatur. Excepteur sint occaecat cupidatat non proident, sunt in culpa qui officia deserunt mollit anim id est laborum.Lorem ipsum dolor sit amet, consectetur adipisicing elit, sed do eiusmod tempor incididunt ut labore et dolore magna aliqua. Ut enim ad minim veniam, quis nostrud exercitation ullamco laboris nisi ut aliquip ex ea commodo consequat. Duis aute irure dolor in reprehenderit in voluptate velit esse cillum dolore eu fugiat nulla pariatur. Excepteur sint occaecat cupidatat non proident, sunt in culpa qui officia deserunt mollit anim id est laborum</p>

  <aside class="abs side">
    <div class="side-head">Featured Products</div>
    <div class="side-session">Session 1 :&nbsp;&nbsp; Multi Estate &amp;<br>Consignment Auction</div>
    <div class="side-img" role="img" aria-label="Silver minivan parked on a driveway"></div>
    <div class="side-btn">FOR MORE DETAILS</div>
    <div class="side-label">Start Date / Time</div>
    <div class="side-text">Wednesday ,<br>April 10,2013 at 2:00 pm</div>
    <div class="side-label" style="margin-top:4px">Location :</div>
    <div class="side-text" style="line-height:14px">1180 Willow Bend Road<br>Ashford , VA 23101</div>
  </aside>

  <h2 class="abs" style="top:764px;left:88px">Upcoming Auctions</h2>
  <h2 class="abs" style="top:764px;left:398px">Past Auctions</h2>

  <div class="abs card" style="top:800px;left:86px">
    <div class="card-img" role="img" aria-label="Two-storey family home with a porch" style="background:linear-gradient(180deg,#5f8f3e,#d8d8d0 50%,#3f6d24)"></div>
    <div class="card-title">3 Bedroom Home in Whiting<br>@ Public Auction</div>
    <div class="card-date">Saturday, May 25, 2013 at 11:00am</div>
    <p class="lorem">Lorem ipsum dolor sit amet, consectetur adipisicing elit, sed do eiusmod tempor incididunt ut labore et dolore magna aliqua. Ut enim ad minim veniam, quis nostrud exercitation ullamco laboris nisi ut aliquip ex ea commodo consequat.</p>
  </div>
  <div class="abs card" style="top:800px;left:242px">
    <div class="card-img" role="img" aria-label="Brick estate house under a blue sky" style="background:linear-gradient(180deg,#3d74c4,#8a8d92 50%,#4e7a2a)"></div>
    <div class="card-title">Estate Auction<br>@ Newjersey</div>
    <div class="card-date">Saturday, June 15, 2013 at 11:00am</div>
    <p class="lorem">Lorem ipsum dolor sit amet, consectetur adipisicing elit, sed do eiusmod tempor incididunt ut labore et dolore magna aliqua. Ut enim ad minim veniam, quis nostrud exercitation ullamco laboris nisi ut aliquip ex ea commodo consequat.</p>
  </div>
  <div class="abs card" style="top:800px;left:398px">
    <div class="card-img" role="img" aria-label="Agent in a suit standing in front of a house" style="background:linear-gradient(90deg,#7aa4cf,#2a2a2a 45%,#d9cfc0 70%,#6f9a3e)"></div>
    <div class="card-title">Real estate Auction</div>
    <div class="card-date">Saturday, June 15, 2012 at 11:00am</div>
    <p class="lorem">Lorem ipsum dolor sit amet, consectetur adipisicing elit, sed do eiusmod tempor incididunt ut labore et dolore magna aliqua. Ut enim ad minim veniam, quis nostrud exercitation ullamco laboris nisi ut aliquip ex ea commodo consequat.</p>
  </div>
  <div class="abs card" style="top:800px;left:554px">
    <div class="card-img" role="img" aria-label="Farmhouse with a wraparound porch" style="background:linear-gradient(180deg,#8fb6e0,#e6e6e0 50%,#5a8a34)"></div>
    <div class="card-title">Greenland Estate Auction</div>
    <div class="card-date">Saturday, June 15, 2013 at 11:00am</div>
    <p class="lorem">Lorem ipsum dolor sit amet, consectetur adipisicing elit, sed do eiusmod tempor incididunt ut labore et dolore magna aliqua. Ut enim ad minim veniam, quis nostrud exercitation ullamco laboris nisi ut aliquip ex ea commodo consequat.</p>
  </div>

  <h2 class="abs partners">Partners Logos</h2>
  <div class="abs rule"></div>
  <div class="abs badges" aria-label="Partner associations">
    <span class="badge" style="width:30px;height:34px"></span>
    <span class="badge" style="width:68px;height:34px;border-radius:4px"></span>
    <span class="badge" style="width:66px;height:24px;border-radius:4px"></span>
    <span class="badge" style="width:52px;height:52px;border-radius:50%"></span>
    <span class="badge" style="width:110px;height:48px;border-radius:4px"></span>
  </div>

  <footer class="abs footer">
    <div class="footer-nav">
      <span>Home</span><span class="sep">|</span><span>Upcoming Auctions</span><span class="sep">|</span><span>Past Auctions</span><span class="sep">|</span><span>For Sale</span><span class="sep">|</span><span>Consignments</span><span class="sep">|</span><span>About Us</span><span class="sep">|</span><span>Highlights</span><span class="sep">|</span><span>Contact Us</span>
    </div>
    <div class="footer-copy">Dunmore Enterprises © 2013 | Privacy policy</div>
  </footer>
</div>
</body>
</html>
```